Commercial Auto Insurance Application and Commercial Property Insurance Application

Hi I need a fillable application for my business to send to potential clients for Commercial Auto Insurance and Commercial Property Insurance. I have attached an example application I currently use for another line of insurance.
Commercial Auto Insurance Application
On the first page I would need the following:
- Business Name: (fill in area for text)
- Effective Date: (fill in area for text)
- How do you structure your business? (Check box for “Sole Proprietor”, “Partnership”, “Corporation”, “LLC”)
- Contact Name: (fill in area for text) / Phone Number: (fill in area for text) / Contact Email (fill in area for text)
- Mailing address: (fill in area for text)
- Garaging location: (fill in area for text)
- Owner Name: (fill in area for text)
- Description of Operations: (fill in area for text)
- How long has the operation been in business? (fill in area for text)
- How many years of experience does your management have in the truck/transportation industry? (fill in area for text)
Coverages
Liability Combined Single Limit: ($1,000,000 (checkbox) / $500,000 (checkbox / $300,000 (checkbox) / Other: (fill in area for text)
Uninsured Motorist CSL: (fill in area for text) (checkbox for “Rejected”)
Medical Payments: (fill in area for text)
Physical Damage: (fill in area for text) (checkbox for Rejected)
Liability Deducible: ($500 checkbox, $1,000 checkbox, $2,500 checkbox, $5,000 checkbox)
Physical Damage Deductible: ($500 checkbox, $1,000 checkbox, $2,500 checkbox, $5,000 checkbox)
Driving radius: (fill in area for text)
How many years have you had your own continuous commercial auto insurance coverage for the current business name? (fill in area for text)
Do any of your vehicles travel across state lines? Yes (checkbox)/ No (checkbox)
If yes, please list all states in which vehicles operate: (fill in area for text)
What is the maximum radius traveled for your customer's business?
0-25 miles (checkbox)
26-50 miles (checkbox)
51-75 miles (checkbox)
76-100 miles (checkbox)
101-150 miles (checkbox)
151-200 miles (checkbox)
201-300 miles (checkbox)
300+ miles (checkbox)
Would you like physical damage coverage for this vehicle? (should be for each vehicle listed)
On the 2nd page of the application I would need the following:
I would need to have it where people can fill in the vehicle information such as VIN:, Year:, Make:, Model:, Type of Vehicle:, Trailers:, Value:
I would also need to have it where people can fill in the drivers with their driver info including Name:, DOB:, DL #:, DL State:, Class of License:, Married: Yes/No, Number of years driving similar vehicle:
Please make it where you can fill in 20 vehicle's information and 20 driver's info.
For the 2nd Application I would need one for Property Insurance
On the Commercial Property Application I would need the following:
- Building Address: (fill in area for text)
- Building Description: (fill in area for text)
- Building Amount: $(fill in area for text)
- Business Personal Property Amount: $ (fill in area for text) (checkbox for Not Needed)
- Building Sq Ft: (fill in area for text)
- Total Area Sq Ft: (fill in area for text)
- Building Construction Type: Wood Frame (checkbox), Steel (checkbox), Fire Resistive (checkbox), Non-Combustible (checkbox), Other (fill in area for text)
- # of stories: (fill in area for text)
- Year Built: (fill in area for text)
- Wiring improvement year: (fill in area for text)
- Roofing improvement year: (fill in area for text)
- Plumbing improvement year: (fill in area for text)
- Heating improvement year: (fill in area for text)
- What is to the right of the building and distance: (fill in area for text)
- What is to the left of the building and distance: (fill in area for text)
- What is in front of the building and distance: (fill in area for text)
- What is behind the building and distance: (fill in area for text)
- Burglar alarm installation and serviced by: (fill in area for text) None (checkbox)
- Does the premises have fire protection? Sprinkler system (checkbox), Fire detection (checkbox), Other: (fill in area for text) None (checkbox)

```html
<!DOCTYPE html>
<html lang="en">
<head>
<meta charset="utf-8">
<title>Commercial Auto Insurance Application</title>
<link rel="stylesheet" href="https://fonts.googleapis.com/css2?family=Roboto:wght@400;500;700&family=Roboto+Condensed:wght@700&family=Tinos:wght@700&display=swap">
<style>
  :root {
    --blue: #012a84;
    --green: #1a9a3a;
    --field: #f3f3f3;
    --ink: #2e2e2e;
    --line: #c9c9c9;
    --backdrop: #d3d3d3;
    --white: #ffffff;
  }
  * { box-sizing: border-box; margin: 0; padding: 0; }
  html, body { width: 1200px; height: 873px; overflow: hidden; }
  body { background: var(--backdrop); font-family: "Roboto", sans-serif; color: var(--ink); position: relative; }

  .page { position: absolute; top: 37px; width: 546px; height: 799px; background: var(--white); box-shadow: 0 2px 8px rgba(0,0,0,.18); }
  .page--one { left: 40px; }
  .page--two { left: 615px; }

  .page-header { position: absolute; left: 0; top: 0; width: 546px; height: 70px; }
  .page-header svg { position: absolute; left: 0; top: 0; }
  .brand { position: absolute; left: 36px; top: 30px; width: 104px; color: var(--blue); font-weight: 700; text-align: center; }
  .brand__name { font-size: 15.5px; letter-spacing: .3px; line-height: 1; display: block; }
  .brand__tag { font-size: 5.6px; letter-spacing: 1.6px; display: block; margin-top: 4px; }

  .abs { position: absolute; }
  .label { position: absolute; font-size: 6.6px; line-height: 1.2; white-space: nowrap; }
  .label--strong { font-weight: 700; }
  .field { position: absolute; height: 18.5px; background: var(--field); }
  .check { position: absolute; width: 22px; height: 19px; background: var(--field); }
  .check-label { position: absolute; font-size: 6.6px; line-height: 1.2; white-space: nowrap; }

  .section-tab { position: absolute; left: 43px; top: 316px; width: 127px; height: 26px; background: linear-gradient(90deg, var(--blue), var(--green)); color: var(--white); font-family: "Roboto Condensed", sans-serif; font-weight: 700; font-size: 11px; display: flex; align-items: center; justify-content: center; letter-spacing: .2px; }
  .coverage-box { position: absolute; left: 43px; top: 342px; width: 458px; height: 188px; border: 1px solid var(--blue); }

  .tick-list { position: absolute; left: 43px; top: 696px; display: grid; grid-template-columns: repeat(5, 96.5px); row-gap: 5.2px; }
  .tick-item { display: flex; align-items: center; gap: 4px; font-size: 6.6px; height: 9.8px; white-space: nowrap; }
  .tick-item svg { flex: none; }

  .page-footer { position: absolute; left: 0; bottom: 0; width: 546px; height: 21px; background: var(--blue); color: var(--white); font-size: 6.4px; display: flex; align-items: center; justify-content: space-between; padding: 0 47px 0 43px; }
  .page-footer span { display: flex; align-items: center; gap: 4px; }

  .section-title { position: absolute; left: 0; width: 546px; text-align: center; font-family: "Roboto Condensed", sans-serif; font-weight: 700; font-size: 15px; color: var(--blue); letter-spacing: .2px; }
  .grid-wrap { position: absolute; left: 43px; width: 458px; }
  .grid-head-bg { position: absolute; left: 0; top: 0; width: 100%; height: 22px; background: linear-gradient(90deg, var(--blue), var(--green)); }
  .info-table { position: relative; width: 100%; border-collapse: collapse; table-layout: fixed; }
  .info-table th { height: 22px; color: var(--white); font-family: "Roboto Condensed", sans-serif; font-weight: 700; font-size: 6.4px; text-align: center; border-left: 1px solid rgba(255,255,255,.25); background: transparent; }
  .info-table th:first-child { border-left: none; }
  .info-table td { height: 19.3px; border: 0.6px solid var(--line); }
</style>
</head>
<body>

<!-- PAGE ONE -->
<section class="page page--one">
  <header class="page-header">
    <svg width="546" height="70" viewBox="0 0 546 70">
      <polygon points="147,0 546,0 546,35 160.5,35" fill="var(--blue)"/>
      <polygon points="160.5,35 546,35 546,70 174,70" fill="var(--green)"/>
      <text x="201" y="27" font-family="Tinos, serif" font-weight="700" font-size="22" fill="#fff" textLength="236" lengthAdjust="spacingAndGlyphs">COMMERCIAL AUTO</text>
      <text x="201" y="60" font-family="Tinos, serif" font-weight="700" font-size="22" fill="#fff" textLength="300" lengthAdjust="spacingAndGlyphs">INSURANCE APPLICATION</text>
    </svg>
    <div class="brand"><span class="brand__name">PRAIRIEWAY</span><span class="brand__tag">INSURANCE SERVICES</span></div>
  </header>

  <div class="label" style="left:43px;top:93px">Business Name</div>
  <div class="field" style="left:43px;top:105px;width:226px"></div>
  <div class="label" style="left:276px;top:93px">Effective Date</div>
  <div class="field" style="left:276px;top:105px;width:225px"></div>
  <svg class="abs" style="left:491px;top:110px" width="7" height="7" viewBox="0 0 7 7"><rect x=".5" y="1" width="6" height="5.5" fill="none" stroke="#b5b5b5" stroke-width=".7"/><line x1=".5" y1="2.6" x2="6.5" y2="2.6" stroke="#b5b5b5" stroke-width=".7"/></svg>

  <div class="label label--strong" style="left:43px;top:134px">How do you structure your business?</div>
  <div class="check" style="left:43px;top:149px"></div><div class="check-label" style="left:68px;top:155px">Sole Proprietor</div>
  <div class="check" style="left:174px;top:149px"></div><div class="check-label" style="left:199px;top:155px">Partnership</div>
  <div class="check" style="left:304px;top:149px"></div><div class="check-label" style="left:329px;top:155px">Corporation</div>
  <div class="check" style="left:434px;top:149px"></div><div class="check-label" style="left:459px;top:155px">LLC</div>

  <div class="label" style="left:43px;top:183px">Contact Name</div>
  <div class="label" style="left:198px;top:183px">Phone Number</div>
  <div class="label" style="left:353px;top:183px">Contact Email</div>
  <div class="field" style="left:43px;top:195px;width:148px"></div>
  <div class="field" style="left:198px;top:195px;width:148px"></div>
  <div class="field" style="left:353px;top:195px;width:148px"></div>

  <div class="label" style="left:43px;top:222px">Mailing address</div>
  <div class="label" style="left:198px;top:222px">Garaging location</div>
  <div class="label" style="left:353px;top:222px">Owner Name</div>
  <div class="field" style="left:43px;top:233px;width:148px"></div>
  <div class="field" style="left:198px;top:233px;width:148px"></div>
  <div class="field" style="left:353px;top:233px;width:148px"></div>

  <div class="label" style="left:43px;top:261px">Description of Operations</div>
  <div class="label" style="left:198px;top:261px">How long has the operation been in business?</div>
  <div class="label" style="left:353px;top:261px">How many years of experience does your<br>management have in the truck/transportation industry?</div>
  <div class="field" style="left:43px;top:281px;width:148px"></div>
  <div class="field" style="left:198px;top:281px;width:148px"></div>
  <div class="field" style="left:353px;top:281px;width:148px"></div>

  <div class="section-tab">COVERAGES</div>
  <div class="coverage-box"></div>

  <div class="label label--strong" style="left:58px;top:350px">How do you structure your business?</div>
  <div class="label" style="left:353px;top:363px">Other</div>
  <div class="check" style="left:58px;top:375px"></div><div class="check-label" style="left:83px;top:381px">$1,000,000</div>
  <div class="check" style="left:165px;top:375px"></div><div class="check-label" style="left:190px;top:381px">$500,000</div>
  <div class="check" style="left:257px;top:375px"></div><div class="check-label" style="left:282px;top:381px">$300,000</div>
  <div class="field" style="left:353px;top:375px;width:133px"></div>

  <div class="label" style="left:58px;top:404px">Uninsured Motorist CSL</div>
  <div class="field" style="left:58px;top:416px;width:140px"></div>
  <div class="check" style="left:208px;top:416px"></div><div class="check-label" style="left:234px;top:422px">Rejected</div>
  <div class="label" style="left:271px;top:404px">Medical Payments</div>
  <div class="field" style="left:271px;top:416px;width:215px"></div>

  <div class="label" style="left:58px;top:445px">Physical Damage</div>
  <div class="field" style="left:58px;top:457px;width:140px"></div>
  <div class="check" style="left:208px;top:457px"></div><div class="check-label" style="left:234px;top:463px">Rejected</div>
  <div class="label label--strong" style="left:271px;top:445px">Liability Deducible</div>
  <div class="check" style="left:271px;top:457px"></div><div class="check-label" style="left:296px;top:463px">$500</div>
  <div class="check" style="left:327px;top:457px"></div><div class="check-label" style="left:352px;top:463px">$1,000</div>
  <div class="check" style="left:385px;top:457px"></div><div class="check-label" style="left:410px;top:463px">$2,500</div>
  <div class="check" style="left:442px;top:457px"></div><div class="check-label" style="left:467px;top:463px">$5,000</div>

  <div class="label label--strong" style="left:58px;top:487px">Physical Damage Deductible</div>
  <div class="check" style="left:58px;top:500px"></div><div class="check-label" style="left:83px;top:506px">$500</div>
  <div class="check" style="left:185px;top:500px"></div><div class="check-label" style="left:210px;top:506px">$1,000</div>
  <div class="check" style="left:314px;top:500px"></div><div class="check-label" style="left:339px;top:506px">$2,500</div>
  <div class="check" style="left:443px;top:500px"></div><div class="check-label" style="left:468px;top:506px">$5,000</div>

  <div class="label" style="left:43px;top:545px">Driving radius</div>
  <div class="field" style="left:43px;top:556px;width:215px"></div>
  <div class="label label--strong" style="left:271px;top:540px">Physical Damage Deductible</div>
  <div class="check" style="left:271px;top:555px"></div><div class="check-label" style="left:296px;top:561px">Yes</div>
  <div class="check" style="left:327px;top:555px"></div><div class="check-label" style="left:352px;top:561px">No</div>

  <div class="label" style="left:43px;top:587px">How many years have you had your own continuous commercial auto insurance coverage for the current business name?</div>
  <div class="field" style="left:43px;top:598px;width:458px"></div>

  <div class="label label--strong" style="left:43px;top:628px">What is the maximum radius traveled for your customer's business?</div>
  <div class="check" style="left:43px;top:644px"></div><div class="check-label" style="left:68px;top:645px">0-25<br>miles</div>
  <div class="check" style="left:103px;top:644px"></div><div class="check-label" style="left:128px;top:645px">26-50<br>miles</div>
  <div class="check" style="left:163px;top:644px"></div><div class="check-label" style="left:188px;top:645px">51-75<br>miles</div>
  <div class="check" style="left:221px;top:644px"></div><div class="check-label" style="left:246px;top:645px">76-100<br>miles</div>
  <div class="check" style="left:278px;top:644px"></div><div class="check-label" style="left:303px;top:645px">101-150<br>miles</div>
  <div class="check" style="left:338px;top:644px"></div><div class="check-label" style="left:363px;top:645px">151-200<br>miles</div>
  <div class="check" style="left:398px;top:644px"></div><div class="check-label" style="left:423px;top:645px">201-300<br>miles</div>
  <div class="check" style="left:461px;top:644px"></div><div class="check-label" style="left:486px;top:645px">300+<br>miles</div>

  <div class="label label--strong" style="left:43px;top:679px">Would you like physical damage coverage for this vehicle?</div>
  <div class="tick-list">
    <!-- 20 checklist items -->
    <div class="tick-item"><svg width="6" height="6" viewBox="0 0 6 6"><rect x=".4" y=".4" width="5.2" height="5.2" fill="none" stroke="var(--green)" stroke-width=".7"/><path d="M1.4 3 2.6 4.2 5.6 .9" fill="none" stroke="var(--green)" stroke-width="1"/></svg>Lorem ipsum dolor sit</div>
    <div class="tick-item"><svg width="6" height="6" viewBox="0 0 6 6"><rect x=".4" y=".4" width="5.2" height="5.2" fill="none" stroke="var(--green)" stroke-width=".7"/><path d="M1.4 3 2.6 4.2 5.6 .9" fill="none" stroke="var(--green)" stroke-width="1"/></svg>Lorem ipsum dolor sit</div>
    <div class="tick-item"><svg width="6" height="6" viewBox="0 0 6 6"><rect x=".4" y=".4" width="5.2" height="5.2" fill="none" stroke="var(--green)" stroke-width=".7"/><path d="M1.4 3 2.6 4.2 5.6 .9" fill="none" stroke="var(--green)" stroke-width="1"/></svg>Lorem ipsum dolor sit</div>
    <div class="tick-item"><svg width="6" height="6" viewBox="0 0 6 6"><rect x=".4" y=".4" width="5.2" height="5.2" fill="none" stroke="var(--green)" stroke-width=".7"/><path d="M1.4 3 2.6 4.2 5.6 .9" fill="none" stroke="var(--green)" stroke-width="1"/></svg>Lorem ipsum dolor sit</div>
    <div class="tick-item"><svg width="6" height="6" viewBox="0 0 6 6"><rect x=".4" y=".4" width="5.2" height="5.2" fill="none" stroke="var(--green)" stroke-width=".7"/><path d="M1.4 3 2.6 4.2 5.6 .9" fill="none" stroke="var(--green)" stroke-width="1"/></svg>Lorem ipsum dolor sit</div>
    <div class="tick-item"><svg width="6" height="6" viewBox="0 0 6 6"><rect x=".4" y=".4" width="5.2" height="5.2" fill="none" stroke="var(--green)" stroke-width=".7"/><path d="M1.4 3 2.6 4.2 5.6 .9" fill="none" stroke="var(--green)" stroke-width="1"/></svg>Lorem ipsum dolor sit</div>
    <div class="tick-item"><svg width="6" height="6" viewBox="0 0 6 6"><rect x=".4" y=".4" width="5.2" height="5.2" fill="none" stroke="var(--green)" stroke-width=".7"/><path d="M1.4 3 2.6 4.2 5.6 .9" fill="none" stroke="var(--green)" stroke-width="1"/></svg>Lorem ipsum dolor sit</div>
    <div class="tick-item"><svg width="6" height="6" viewBox="0 0 6 6"><rect x=".4" y=".4" width="5.2" height="5.2" fill="none" stroke="var(--green)" stroke-width=".7"/><path d="M1.4 3 2.6 4.2 5.6 .9" fill="none" stroke="var(--green)" stroke-width="1"/></svg>Lorem ipsum dolor sit</div>
    <div class="tick-item"><svg width="6" height="6" viewBox="0 0 6 6"><rect x=".4" y=".4" width="5.2" height="5.2" fill="none" stroke="var(--green)" stroke-width=".7"/><path d="M1.4 3 2.6 4.2 5.6 .9" fill="none" stroke="var(--green)" stroke-width="1"/></svg>Lorem ipsum dolor sit</div>
    <div class="tick-item"><svg width="6" height="6" viewBox="0 0 6 6"><rect x=".4" y=".4" width="5.2" height="5.2" fill="none" stroke="var(--green)" stroke-width=".7"/><path d="M1.4 3 2.6 4.2 5.6 .9" fill="none" stroke="var(--green)" stroke-width="1"/></svg>Lorem ipsum dolor sit</div>
    <div class="tick-item"><svg width="6" height="6" viewBox="0 0 6 6"><rect x=".4" y=".4" width="5.2" height="5.2" fill="none" stroke="var(--green)" stroke-width=".7"/><path d="M1.4 3 2.6 4.2 5.6 .9" fill="none" stroke="var(--green)" stroke-width="1"/></svg>Lorem ipsum dolor sit</div>
    <div class="tick-item"><svg width="6" height="6" viewBox="0 0 6 6"><rect x=".4" y=".4" width="5.2" height="5.2" fill="none" stroke="var(--green)" stroke-width=".7"/><path d="M1.4 3 2.6 4.2 5.6 .9" fill="none" stroke="var(--green)" stroke-width="1"/></svg>Lorem ipsum dolor sit</div>
    <div class="tick-item"><svg width="6" height="6" viewBox="0 0 6 6"><rect x=".4" y=".4" width="5.2" height="5.2" fill="none" stroke="var(--green)" stroke-width=".7"/><path d="M1.4 3 2.6 4.2 5.6 .9" fill="none" stroke="var(--green)" stroke-width="1"/></svg>Lorem ipsum dolor sit</div>
    <div class="tick-item"><svg width="6" height="6" viewBox="0 0 6 6"><rect x=".4" y=".4" width="5.2" height="5.2" fill="none" stroke="var(--green)" stroke-width=".7"/><path d="M1.4 3 2.6 4.2 5.6 .9" fill="none" stroke="var(--green)" stroke-width="1"/></svg>Lorem ipsum dolor sit</div>
    <div class="tick-item"><svg width="6" height="6" viewBox="0 0 6 6"><rect x=".4" y=".4" width="5.2" height="5.2" fill="none" stroke="var(--green)" stroke-width=".7"/><path d="M1.4 3 2.6 4.2 5.6 .9" fill="none" stroke="var(--green)" stroke-width="1"/></svg>Lorem ipsum dolor sit</div>
    <div class="tick-item"><svg width="6" height="6" viewBox="0 0 6 6"><rect x=".4" y=".4" width="5.2" height="5.2" fill="none" stroke="var(--green)" stroke-width=".7"/><path d="M1.4 3 2.6 4.2 5.6 .9" fill="none" stroke="var(--green)" stroke-width="1"/></svg>Lorem ipsum dolor sit</div>
    <div class="tick-item"><svg width="6" height="6" viewBox="0 0 6 6"><rect x=".4" y=".4" width="5.2" height="5.2" fill="none" stroke="var(--green)" stroke-width=".7"/><path d="M1.4 3 2.6 4.2 5.6 .9" fill="none" stroke="var(--green)" stroke-width="1"/></svg>Lorem ipsum dolor sit</div>
    <div class="tick-item"><svg width="6" height="6" viewBox="0 0 6 6"><rect x=".4" y=".4" width="5.2" height="5.2" fill="none" stroke="var(--green)" stroke-width=".7"/><path d="M1.4 3 2.6 4.2 5.6 .9" fill="none" stroke="var(--green)" stroke-width="1"/></svg>Lorem ipsum dolor sit</div>
    <div class="tick-item"><svg width="6" height="6" viewBox="0 0 6 6"><rect x=".4" y=".4" width="5.2" height="5.2" fill="none" stroke="var(--green)" stroke-width=".7"/><path d="M1.4 3 2.6 4.2 5.6 .9" fill="none" stroke="var(--green)" stroke-width="1"/></svg>Lorem ipsum dolor sit</div>
    <div class="tick-item"><svg width="6" height="6" viewBox="0 0 6 6"><rect x=".4" y=".4" width="5.2" height="5.2" fill="none" stroke="var(--green)" stroke-width=".7"/><path d="M1.4 3 2.6 4.2 5.6 .9" fill="none" stroke="var(--green)" stroke-width="1"/></svg>Lorem ipsum dolor sit</div>
  </div>

  <footer class="page-footer">
    <span><svg width="5" height="7" viewBox="0 0 5 7"><path d="M2.5 0A2.5 2.5 0 0 0 0 2.5C0 4.4 2.5 7 2.5 7S5 4.4 5 2.5A2.5 2.5 0 0 0 2.5 0Zm0 3.5a1 1 0 1 1 0-2 1 1 0 0 1 0 2Z" fill="#fff"/></svg>Prairieway Insurance Services 4820 Meridian Ave Suite 310 Lakeview, CA 90210</span>
    <span><svg width="6" height="6" viewBox="0 0 24 24"><path d="M6.6 10.8a15.1 15.1 0 0 0 6.6 6.6l2.2-2.2c.3-.3.7-.4 1-.2 1.1.4 2.3.6 3.6.6.6 0 1 .4 1 1V20c0 .6-.4 1-1 1A17 17 0 0 1 3 4c0-.6.4-1 1-1h3.5c.6 0 1 .4 1 1 0 1.3.2 2.5.6 3.6.1.3 0 .7-.2 1Z" fill="#fff"/></svg>Phone : (555) 014-2290</span>
  </footer>
</section>

<!-- PAGE TWO -->
<section class="page page--two">
  <header class="page-header">
    <svg width="546" height="70" viewBox="0 0 546 70">
      <polygon points="147,0 546,0 546,35 160.5,35" fill="var(--blue)"/>
      <polygon points="160.5,35 546,35 546,70 174,70" fill="var(--green)"/>
      <text x="201" y="27" font-family="Tinos, serif" font-weight="700" font-size="22" fill="#fff" textLength="236" lengthAdjust="spacingAndGlyphs">COMMERCIAL AUTO</text>
      <text x="201" y="60" font-family="Tinos, serif" font-weight="700" font-size="22" fill="#fff" textLength="300" lengthAdjust="spacingAndGlyphs">INSURANCE APPLICATION</text>
    </svg>
    <div class="brand"><span class="brand__name">PRAIRIEWAY</span><span class="brand__tag">INSURANCE SERVICES</span></div>
  </header>

  <h2 class="section-title" style="top:83px">VEHICLE INFORMATION</h2>
  <div class="grid-wrap" style="top:108px">
    <div class="grid-head-bg"></div>
    <table class="info-table">
      <thead><tr><th>VIN</th><th>YEAR</th><th>MAKE</th><th>MODEL</th><th>TYPE OF VEHICLE</th><th>TRAILERS</th><th>VALUE</th></tr></thead>
      <tbody>
        <tr><td></td><td></td><td></td><td></td><td></td><td></td><td></td></tr>
        <tr><td></td><td></td><td></td><td></td><td></td><td></td><td></td></tr>
        <tr><td></td><td></td><td></td><td></td><td></td><td></td><td></td></tr>
        <tr><td></td><td></td><td></td><td></td><td></td><td></td><td></td></tr>
        <tr><td></td><td></td><td></td><td></td><td></td><td></td><td></td></tr>
        <tr><td></td><td></td><td></td><td></td><td></td><td></td><td></td></tr>
        <tr><td></td><td></td><td></td><td></td><td></td><td></td><td></td></tr>
        <tr><td></td><td></td><td></td><td></td><td></td><td></td><td></td></tr>
        <tr><td></td><td></td><td></td><td></td><td></td><td></td><td></td></tr>
        <tr><td></td><td></td><td></td><td></td><td></td><td></td><td></td></tr>
        <tr><td></td><td></td><td></td><td></td><td></td><td></td><td></td></tr>
        <tr><td></td><td></td><td></td><td></td><td></td><td></td><td></td></tr>
        <tr><td></td><td></td><td></td><td></td><td></td><td></td><td></td></tr>
        <tr><td></td><td></td><td></td><td></td><td></td><td></td><td></td></tr>
        <tr><td></td><td></td><td></td><td></td><td></td><td></td><td></td></tr>
      </tbody>
    </table>
  </div>

  <h2 class="section-title" style="top:436px">DRIVER INFORMATION</h2>
  <div class="grid-wrap" style="top:460px">
    <div class="grid-head-bg"></div>
    <table class="info-table">
      <thead><tr><th>NAME</th><th>DOB</th><th>DL #</th><th>DL STATE</th><th>CLASS OF LICENSE</th><th>MARRIED</th><th>NO.OF VEHICLE</th></tr></thead>
      <tbody>
        <tr><td></td><td></td><td></td><td></td><td></td><td></td><td></td></tr>
        <tr><td></td><td></td><td></td><td></td><td></td><td></td><td></td></tr>
        <tr><td></td><td></td><td></td><td></td><td></td><td></td><td></td></tr>
        <tr><td></td><td></td><td></td><td></td><td></td><td></td><td></td></tr>
        <tr><td></td><td></td><td></td><td></td><td></td><td></td><td></td></tr>
        <tr><td></td><td></td><td></td><td></td><td></td><td></td><td></td></tr>
        <tr><td></td><td></td><td></td><td></td><td></td><td></td><td></td></tr>
        <tr><td></td><td></td><td></td><td></td><td></td><td></td><td></td></tr>
        <tr><td></td><td></td><td></td><td></td><td></td><td></td><td></td></tr>
        <tr><td></td><td></td><td></td><td></td><td></td><td></td><td></td></tr>
        <tr><td></td><td></td><td></td><td></td><td></td><td></td><td></td></tr>
        <tr><td></td><td></td><td></td><td></td><td></td><td></td><td></td></tr>
        <tr><td></td><td></td><td></td><td></td><td></td><td></td><td></td></tr>
        <tr><td></td><td></td><td></td><td></td><td></td><td></td><td></td></tr>
        <tr><td></td><td></td><td></td><td></td><td></td><td></td><td></td></tr>
      </tbody>
    </table>
  </div>

  <footer class="page-footer">
    <span><svg width="5" height="7" viewBox="0 0 5 7"><path d="M2.5 0A2.5 2.5 0 0 0 0 2.5C0 4.4 2.5 7 2.5 7S5 4.4 5 2.5A2.5 2.5 0 0 0 2.5 0Zm0 3.5a1 1 0 1 1 0-2 1 1 0 0 1 0 2Z" fill="#fff"/></svg>Prairieway Insurance Services 4820 Meridian Ave Suite 310 Lakeview, CA 90210</span>
    <span><svg width="6" height="6" viewBox="0 0 24 24"><path d="M6.6 10.8a15.1 15.1 0 0 0 6.6 6.6l2.2-2.2c.3-.3.7-.4 1-.2 1.1.4 2.3.6 3.6.6.6 0 1 .4 1 1V20c0 .6-.4 1-1 1A17 17 0 0 1 3 4c0-.6.4-1 1-1h3.5c.6 0 1 .4 1 1 0 1.3.2 2.5.6 3.6.1.3 0 .7-.2 1Z" fill="#fff"/></svg>Phone : (555) 014-2290</span>
  </footer>
</section>

</body>
</html>
```